Lorvex Tilo medical cannibis cultivation company

tag - Tilo rise
Lorvex Tilo medical cannabis cultivation - logo is selected- can we please see bold examples with our selection. We are mainly dealing with medical companies and professionals. We would like to be stand out in the crowd with our designs. Welcome any and all attempts. Thanks

Target Market(s)

Medical and Professional

Industry/Entity Type

Medical And Science

Font styles to use
Sans Serif

Colors

Designer to choose colors to be used in the design.

Requirements
Must have
• Bright colour and be bold- Love the teal and magenta that is currently on the dark background design.
Nice to have
• shading and the 3D affect- The shadowed appearance.
Should not have
• Anything related to illegal activity or un professional manners

```html
<!DOCTYPE html>
<html lang="en">
<head>
<meta charset="utf-8">
<title>Lorvex Tilo — Business Card</title>
<link rel="stylesheet" href="https://fonts.googleapis.com/css2?family=Roboto+Condensed:wght@700&family=Roboto:wght@400;500&display=swap">
<style>
  :root {
    --backdrop: #2b2b2e;
    --card: #1d1d20;
    --card-edge: #303034;
    --teal: #1ab6ea;
    --magenta: #b04fc2;
    --ink: #f2f2f2;
    --rule: #8a8a8e;
    --ring: #9b9ba0;
  }
  * { box-sizing: border-box; margin: 0; padding: 0; }
  html, body { width: 1200px; height: 900px; overflow: hidden; }
  body {
    background: var(--backdrop);
    font-family: "Roboto", Arial, sans-serif;
    position: relative;
  }
  .card {
    position: absolute;
    left: 320px;
    width: 560px;
    height: 320px;
    background: var(--card);
    border: 1px solid var(--card-edge);
    box-shadow: 0 18px 40px rgba(0,0,0,0.45);
  }
  .card--front { top: 90px; }
  .card--back { top: 490px; }

  /* Front */
  .brand {
    position: absolute;
    left: 0; right: 0; top: 70px;
    display: flex; flex-direction: column; align-items: center;
  }
  .brand__ring {
    width: 92px; height: 92px;
    border: 3px solid var(--ring);
    border-radius: 50%;
    margin-bottom: 14px;
  }
  .brand__name {
    font-family: "Roboto Condensed", "Arial Narrow", sans-serif;
    font-weight: 700;
    font-size: 40px;
    letter-spacing: 1px;
    text-transform: uppercase;
    color: var(--teal);
    line-height: 1;
  }
  .brand__tag {
    display: flex; align-items: center; gap: 8px;
    margin-top: 6px;
    font-family: "Roboto Condensed", "Arial Narrow", sans-serif;
    font-weight: 700;
    font-size: 13px;
    letter-spacing: 2px;
    text-transform: uppercase;
    color: var(--ring);
  }
  .brand__tag::before, .brand__tag::after {
    content: ""; width: 70px; height: 1px; background: var(--rule);
  }

  /* Back */
  .person {
    position: absolute;
    right: 292px; top: 78px;
    text-align: right;
  }
  .person__name {
    font-family: "Roboto Condensed", "Arial Narrow", sans-serif;
    font-weight: 700;
    font-size: 33px;
    color: var(--teal);
    text-transform: uppercase;
    line-height: 1;
  }
  .person__role {
    font-family: "Roboto Condensed", "Arial Narrow", sans-serif;
    font-weight: 700;
    font-size: 17px;
    color: var(--magenta);
    text-transform: uppercase;
    margin-top: 4px;
  }
  .divider {
    position: absolute;
    left: 282px; top: 56px;
    width: 1px; height: 140px;
    background: linear-gradient(var(--card), var(--rule) 30%, var(--rule) 70%, var(--card));
  }
  .contacts {
    position: absolute;
    left: 302px; top: 66px;
    list-style: none;
  }
  .contacts li {
    display: flex; align-items: center; gap: 10px;
    font-size: 16px; font-weight: 500;
    color: var(--ink);
    height: 24px;
  }
  .contacts svg, .address svg { width: 16px; height: 16px; fill: var(--teal); flex: none; }
  .address {
    position: absolute;
    left: 40px; bottom: 40px;
    display: flex; align-items: center; gap: 6px;
    font-size: 17px; font-weight: 500;
    color: var(--ink);
  }
</style>
</head>
<body>

<section class="card card--front">
  <div class="brand">
    <div class="brand__ring"></div>
    <div class="brand__name">Lorvex Tilo</div>
    <div class="brand__tag">Tilo rise</div>
  </div>
</section>

<section class="card card--back">
  <div class="person">
    <div class="person__name">Maren Odell</div>
    <div class="person__role">CEO/Founder</div>
  </div>
  <div class="divider"></div>
  <ul class="contacts">
    <li>
      <svg viewBox="0 0 16 16" aria-hidden="true"><path d="M3.6 1.5l2.3 2.6-1.2 1.9c.9 2 2.4 3.5 4.4 4.4l1.9-1.2 2.6 2.3-1.3 2.2C7.4 14.6 1.4 8.6 1.3 3.9z"/></svg>
      555 204 7716
    </li>
    <li>
      <svg viewBox="0 0 16 16" aria-hidden="true"><path d="M4.5 1h7a1 1 0 0 1 1 1v12a1 1 0 0 1-1 1h-7a1 1 0 0 1-1-1V2a1 1 0 0 1 1-1zm.5 2v9h6V3zm3 9.8a.8.8 0 1 0 0 1.6.8.8 0 0 0 0-1.6z"/></svg>
      555 318 4092
    </li>
    <li>
      <svg viewBox="0 0 16 16" aria-hidden="true"><path d="M4 1h8v4H4zM2 6h12a1 1 0 0 1 1 1v5h-3v3H4v-3H1V7a1 1 0 0 1 1-1zm3 5v3h6v-3z"/></svg>
      555 627 0385
    </li>
    <li>
      <svg viewBox="0 0 16 16" aria-hidden="true"><path d="M1 3h14v1.2L8 8.6 1 4.2zm0 2.6l7 4.4 7-4.4V13H1z"/></svg>
      maren@lorvextilo.com
    </li>
    <li>
      <svg viewBox="0 0 16 16" aria-hidden="true"><path d="M8 1a7 7 0 1 0 0 14A7 7 0 0 0 8 1zm0 1.4c.8.8 1.5 2.2 1.7 4H6.3C6.5 4.6 7.2 3.2 8 2.4zM2.5 7.4h2.4c.1 1.5.4 2.8 1 3.9a5.6 5.6 0 0 1-3.4-3.9zm3.8 0h3.4c-.2 1.8-.9 3.2-1.7 4-.8-.8-1.5-2.2-1.7-4zm4.8 0h2.4a5.6 5.6 0 0 1-3.4 3.9c.6-1.1.9-2.4 1-3.9z"/></svg>
      www.lorvextilo.com
    </li>
  </ul>
  <div class="address">
    <svg viewBox="0 0 16 16" aria-hidden="true"><path d="M8 0.8a5 5 0 0 0-5 5c0 3.8 5 9.4 5 9.4s5-5.6 5-9.4a5 5 0 0 0-5-5zm0 7a2 2 0 1 1 0-4 2 2 0 0 1 0 4z"/></svg>
    214 Willowmere Road, Halden Bay, Alaska 30918
  </div>
</section>

</body>
</html>
```